Profesional personal website needs design and business card

I need a business card with my professional name as a logo "Dorian Vitality" for my business. I am a Wellness Coach, consultant and trainer. So it should be professional, wellness oriented and modern.

Target Market(s)

Private clients, governments, corporations. Luxury and high market.

Industry/Entity Type

Health And Wellness

Contact Information for Business Card

Dorian Vitality should be the logo

Colors

Designer to choose colors to be used in the design.

Requirements
Must have
• Dorian Vitality
• Name: Tomás Lirandel
• Wellness Coach, Consultant & Trainer.
• Website: www.dorianvitality-example.com
• Phone:
• Spain (+34) 612 480 317
• (USA) +1 (555) 610 4829
Nice to have
• The most important is the design of "Dorian Vitality", as this is going to be my personal brand logo. It should be professional, wellness, high end and actual.
Should not have
• no golds, no baroque style..

```html
<!DOCTYPE html>
<html lang="en">
<head>
<meta charset="utf-8">
<title>Dorian Vitality – Business Card</title>
<link href="https://fonts.googleapis.com/css2?family=Oswald:wght@300;400;500&display=swap" rel="stylesheet">
<style>
  :root {
    --brand-green: #00a331;
    --accent-orange: #f98200;
    --card-white: #f4f5f7;
    --text-white: #ffffff;
    --backdrop: #e9e6e1;
    --shadow: rgba(0, 0, 0, 0.18);
  }
  * { box-sizing: border-box; margin: 0; padding: 0; }
  html, body {
    width: 1200px;
    height: 800px;
    overflow: hidden;
    background: var(--backdrop);
    font-family: "Oswald", sans-serif;
  }
  .stage {
    width: 1200px;
    height: 800px;
    display: flex;
    align-items: center;
    justify-content: center;
    gap: 60px;
  }
  .card {
    position: relative;
    width: 520px;
    height: 300px;
    overflow: hidden;
    box-shadow: 0 10px 28px var(--shadow);
  }
  .card-back {
    background: var(--brand-green);
    display: flex;
    align-items: center;
    justify-content: center;
  }
  .brand-name {
    font-family: "Oswald", sans-serif;
    font-weight: 500;
    letter-spacing: 0.5px;
    white-space: nowrap;
  }
  .card-back .brand-name {
    color: var(--text-white);
    font-size: 46px;
  }
  .card-front { background: var(--card-white); }
  .front-shapes {
    position: absolute;
    inset: 0;
    width: 100%;
    height: 100%;
  }
  .card-front .brand-name {
    position: absolute;
    top: 52px;
    left: 190px;
    color: var(--brand-green);
    font-size: 42px;
  }
  .contact-area {
    position: absolute;
    left: 0;
    right: 0;
    top: 218px;
    display: flex;
    justify-content: center;
    color: var(--text-white);
  }
  .holder {
    text-align: right;
    padding-right: 14px;
  }
  .holder-name {
    font-size: 19px;
    font-weight: 500;
    line-height: 1.15;
  }
  .holder-role {
    font-size: 9.5px;
    font-weight: 300;
    letter-spacing: 0.2px;
  }
  .divider {
    width: 1px;
    height: 62px;
    background: var(--text-white);
  }
  .contact-list {
    list-style: none;
    padding-left: 14px;
    font-size: 9.5px;
    font-weight: 400;
    letter-spacing: 1.1px;
    line-height: 1.3;
  }
  .contact-item {
    display: flex;
    align-items: flex-start;
    gap: 9px;
    margin-bottom: 5px;
  }
  .contact-icon {
    width: 11px;
    height: 11px;
    flex: none;
    margin-top: 1px;
  }
</style>
</head>
<body>
<main class="stage">
  <section class="card card-back" aria-label="Business card, back">
    <span class="brand-name">Dorian Vitality</span>
  </section>

  <section class="card card-front" aria-label="Business card, front">
    <svg class="front-shapes" viewBox="0 0 520 300" aria-hidden="true">
      <path d="M0,74 Q230,232 520,212 L520,300 L0,300 Z" fill="var(--brand-green)"/>
      <path d="M0,60 Q230,214 500,200" fill="none" stroke="var(--accent-orange)" stroke-width="5" stroke-linecap="round"/>
    </svg>

    <span class="brand-name">Dorian Vitality</span>

    <div class="contact-area">
      <div class="holder">
        <p class="holder-name">Tomás Lirandel</p>
        <p class="holder-role">Wellness Coach, Consultant &amp; Trainer</p>
      </div>
      <div class="divider"></div>
      <ul class="contact-list">
        <li class="contact-item">
          <svg class="contact-icon" viewBox="0 0 24 24" aria-hidden="true"><path d="M6.6 2.5 9.5 6.8 7.6 9c1.3 2.8 4.6 6.1 7.4 7.4l2.2-1.9 4.3 2.9-1.4 3.8C12 21 3 12 2.8 3.9Z" fill="none" stroke="currentColor" stroke-width="1.8" stroke-linejoin="round"/></svg>
          <span>Spain (+34) 612 480 317<br>(USA) +1 (555) 610 4829</span>
        </li>
        <li class="contact-item">
          <svg class="contact-icon" viewBox="0 0 24 24" aria-hidden="true"><g fill="none" stroke="currentColor" stroke-width="1.8"><circle cx="12" cy="12" r="10"/><ellipse cx="12" cy="12" rx="4.5" ry="10"/><path d="M2 12h20M4 6.5h16M4 17.5h16"/></g></svg>
          <span>hello@dorianvitality-example.com</span>
        </li>
        <li class="contact-item">
          <svg class="contact-icon" viewBox="0 0 24 24" aria-hidden="true"><g fill="none" stroke="currentColor" stroke-width="1.8" stroke-linejoin="round"><rect x="2" y="5" width="20" height="14"/><path d="M2 5l10 8 10-8M2 19l7.5-7.5M22 19l-7.5-7.5"/></g></svg>
          <span>www.dorianvitality-example.com</span>
        </li>
      </ul>
    </div>
  </section>
</main>
</body>
</html>
```